Business card design for a dynamic IT consulting company

We need a business card design for a young firm, specialized in the Telecommunications/Consulting industry. The name of the company is Quindor and Partners Business Consulting Ltd. (Short name: Quindor and Partnes)
Quindor = solve read reverse, so we aim to be uncomplicated and solution-oriented. The small pipe in our logo is also related to the word solve. So we need a new business card design, which is simple, eye catching and something non traditional (I would probably prefer a square shaped design rather than a rectangle, but open for suggestions). Attached our logo.

Target Market(s)

Usually our customers are Tier1 Telecoms providers (Q-Netra, Palorix, etc) and their executives.

Industry/Entity Type

Business

Contact Information for Business Card

Name: Bence Tolnavari
Email: b.tolnavari@quindor.hu
Web: www.quindor.hu
Mobile: +36 30 518 2769
Title: Managing Director

Optional:
Company name: Quindor and Partners Ltd.
Address: 1087 Budapest, Tolvenka str. 28/C, Hungary

Font styles to use
Other font styles liked:
• helveticaneue_medium, Prime Regular are used now.

Colors

Designer to choose colors to be used in the design.

Requirements
Must have
• I would like to have a 2 sided design.
Nice to have
• I thought if we make the logo a bit bigger (without the company name), that could go to the back with the company name below. I though, if the pipe in the logo is somehow touchable on the business card, would be nice and unique.

```html
<!DOCTYPE html>
<html lang="en">
<head>
<meta charset="utf-8">
<title>Quindor and Partners – Business Card</title>
<link href="https://fonts.googleapis.com/css2?family=Montserrat:wght@700&family=Work+Sans:wght@300;400;500&display=swap" rel="stylesheet">
<style>
  :root {
    --brand-blue: #1b9ad6;
    --ink: #555555;
    --paper: #ffffff;
    --backdrop: #2a2a2a;
  }
  * { margin: 0; padding: 0; box-sizing: border-box; }
  html, body { width: 1200px; height: 930px; overflow: hidden; }
  body {
    background: var(--backdrop);
    position: relative;
    font-family: "Work Sans", sans-serif;
  }
  .card {
    position: absolute;
    width: 645px;
    height: 369px;
  }
  .card--front {
    left: 278px; top: 76px;
    background: var(--paper);
    border-top: 1px solid var(--brand-blue);
  }
  .card--back {
    left: 277px; top: 486px;
    background: var(--brand-blue);
  }

  /* name band */
  .name-band {
    position: absolute;
    left: 0; top: 50px;
    width: 276px; height: 42px;
    background: var(--brand-blue);
    clip-path: polygon(0 0, 248px 0, 276px 21px, 248px 42px, 0 42px);
  }
  .person-name {
    position: absolute;
    left: 27px; top: 48px;
    color: var(--paper);
    font-family: "Montserrat", sans-serif;
    font-weight: 700;
    font-size: 22px;
    letter-spacing: 0.2px;
  }
  .person-title {
    position: absolute;
    left: 26px; top: 72px;
    color: var(--paper);
    font-weight: 300;
    font-size: 16px;
  }

  /* company name lockup */
  .company {
    position: absolute;
    display: flex;
    align-items: center;
    font-weight: 400;
    white-space: nowrap;
  }
  .company__square { display: block; flex: none; }
  .company--front {
    left: 290px; top: 54px;
    gap: 10px;
    color: var(--ink);
    font-size: 30px;
  }
  .company--front .company__square {
    width: 14px; height: 14px;
    background: var(--brand-blue);
  }
  .company--back {
    left: 0; right: 0; top: 155px;
    justify-content: center;
    gap: 16px;
    color: var(--paper);
    font-size: 46px;
  }
  .company--back .company__square {
    width: 20px; height: 20px;
    background: var(--paper);
  }

  .rule {
    position: absolute;
    left: 33px; right: 28px; top: 249px;
    height: 1px;
    background: var(--brand-blue);
  }

  .contact-list {
    position: absolute;
    left: 31px; top: 274px;
    list-style: none;
    color: var(--ink);
    font-weight: 300;
    font-size: 16px;
    line-height: 20px;
  }
  .contact-list li { display: flex; align-items: center; gap: 10px; }
  .contact-list svg { width: 12px; height: 12px; flex: none; }

  .address {
    position: absolute;
    right: 30px; top: 294px;
    text-align: right;
    font-style: normal;
    color: var(--ink);
    font-weight: 300;
    font-size: 16px;
    line-height: 20px;
  }
</style>
</head>
<body>

<section class="card card--front" aria-label="Business card front">
  <div class="name-band"></div>
  <p class="person-name">Bence Tolnavari</p>
  <p class="person-title">Managing Director</p>

  <div class="company company--front">
    <span class="company__square"></span>
    <span class="company__name">Quindor &amp; Partners</span>
  </div>

  <div class="rule"></div>

  <ul class="contact-list">
    <li>
      <svg viewBox="0 0 12 12" aria-hidden="true"><path d="M3 1 L5 3.5 L4 5 Q5.5 7.5 7.5 8.5 L9 7.5 L11 9.5 L9.5 11 Q4 10 1.5 3 Z" fill="none" stroke="#1b9ad6" stroke-width="1.1" stroke-linejoin="round"/></svg>
      <span>+36 30 518 2769</span>
    </li>
    <li>
      <svg viewBox="0 0 12 12" aria-hidden="true"><rect x="1" y="2.5" width="10" height="7" fill="none" stroke="#1b9ad6" stroke-width="1.1"/><path d="M1 2.5 L6 6.5 L11 2.5" fill="none" stroke="#1b9ad6" stroke-width="1.1"/></svg>
      <span>b.tolnavari@quindor.hu</span>
    </li>
    <li>
      <svg viewBox="0 0 12 12" aria-hidden="true"><circle cx="6" cy="6" r="5" fill="none" stroke="#1b9ad6" stroke-width="1"/><ellipse cx="6" cy="6" rx="2.2" ry="5" fill="none" stroke="#1b9ad6" stroke-width="1"/><path d="M1 6 H11 M2 3.5 H10 M2 8.5 H10" stroke="#1b9ad6" stroke-width="0.8"/></svg>
      <span>www.quindor.hu</span>
    </li>
  </ul>

  <address class="address">
    1087 Budapest,<br>
    Tolvenka str. 28/C, Hungary
  </address>
</section>

<section class="card card--back" aria-label="Business card back">
  <div class="company company--back">
    <span class="company__square"></span>
    <span class="company__name">Quindor &amp; Partners</span>
  </div>
</section>

</body>
</html>
```